Probate (Legal) Wordpress Design with Coding for Online Company

I need a Wordpress design with coding, pictures, content to be provided by me, fully responsive, and development. This is for a 6-7 page design.

Pages Needed: Home/About/Probate/Process/FAQ/Contact Us/Blog.

The home page should be organized as followed:
-Steps in Probate: Gather; Implement; Close (each step will come with content)
-Flat-Fee Price & Savings: Content will go here with a button to contact us (phone number) or just the phone number.
-You Have Questions, We Have Answers: five questions with content. Only one question answer to show at a time when clicked on the question from the list.
-Get to Know Us: a brief description with content about what we do and who we are.

Main image slogan: Helping Californians deal with loss with DIGNITY & UNDERSTATING (you may use a better slogan if you wish).

The Contact page should not have a map since we are an online company. We service the entire state of California in every county and city.

The About page should be simple, direct, and easy on the eye. It should have a brief description of who we are and it should have no more than 6 reasons why the client should hire us.

About our online California company. We are not attorneys but legal document assistants who prepare legal documents for probate estate when someone dies with or without a will and assets need to be distributed. We have a flat-fee for Formal Probate of $999 and $699 for Informal Probate. We are an online company and offer our services to the entire state of California in every county. We do everything over the phone and email. The turn around time for us to prepare the initial legal paperwork for the client is within 3-5 business days. We can prepare, file, serve and manage a probate matter from petition to closing. We are not attorneys so our prices are very affordable compare to the attorney.

The company name for the website will be www.velmarhollow.com, The Velmar Hollow Group.

I do not have a logo yet. The colors of the website should be easy on the eye and calming. THE SITE SHOULD BE SIMPLE AND STRAIGHT TO THE POINT. EASY TO NAVIGATE.

The company phone number should be very visible and should stand out to the client. It should also be clickable and ready to dial for smartphone users.

I do not want a contact form on the homepage. THE MAIN THING IS FOR THE POTENTIAL CLIENT TO CALL OUR OFFICE TO SIGN UP.

I do like some images of family or people since we are dealing with people who just lost a loved one. Not all the images have to be of people.

The site should not look like we practice law or that people can mistake us for attorneys.

Target Market(s)

People who just lost a loved one who had property, assets, in California but died with or without a will or trust. This is for people looking to hire non-attorneys.

Coding

Coded - Design and coding required

Font styles to use
Serif

Colors

Designer to choose colors to be used in the design.

Requirements
Must have
• Refer to Project Description.
Nice to have
• The sample images provided is what I am attracted to for the homepage image.
Should not have

```html
<!DOCTYPE html>
<html lang="en">
<head>
<meta charset="utf-8">
<title>The Velmar Hollow Group</title>
<link href="https://fonts.googleapis.com/css2?family=Oswald:wght@400;500&family=Open+Sans:wght@400;600&family=Montserrat:wght@500;600&display=swap" rel="stylesheet">
<style>
:root{
  --blue:#2a9df4;
  --navy:#1e2b4c;
  --navy-deep:#17213a;
  --ink:#222;
  --body:#444;
  --grey:#f3f3f3;
  --frame:#dde0e6;
  --input:#3a4766;
}
*{margin:0;padding:0;box-sizing:border-box}
html,body{width:1200px;height:2528px;overflow:hidden;background:#fff}
body{font-family:"Open Sans",sans-serif;color:var(--body);position:relative}
.abs{position:absolute}
h2,h3,h4{font-family:"Oswald",sans-serif;font-weight:500}

/* header */
.site-header{position:absolute;left:0;top:0;width:1200px;height:108px;border-top:3px solid var(--blue);background:#fff}
.brand{position:absolute;left:162px;top:22px;display:flex;align-items:center;gap:12px;font-family:"Montserrat",sans-serif;font-weight:600;font-size:19px;color:var(--ink);letter-spacing:.3px}
.brand-mark{width:22px;height:22px;background:var(--blue)}
.phone{position:absolute;left:829px;top:18px;font-family:"Montserrat",sans-serif;font-size:15px;color:var(--blue);display:flex;align-items:center;gap:8px}
.main-nav{position:absolute;left:425px;top:68px;display:flex;gap:0;font-family:"Montserrat",sans-serif;font-size:12.5px;font-weight:600;color:var(--ink)}
.main-nav span{margin-right:40px}
.main-nav .active{color:var(--blue)}
.nav-sep{position:absolute;left:1003px;top:64px;width:1px;height:20px;background:#ccc}
.search{position:absolute;left:1021px;top:69px}

/* hero */
.hero{position:absolute;left:0;top:108px;width:1200px;height:519px;background:linear-gradient(180deg,#9fc7ea 0%,#cfe3f2 45%,#a9b867 62%,#6f8a2e 100%)}
.hero-lead{position:absolute;left:162px;top:318px;font-family:"Oswald",sans-serif;font-size:26px;color:#333;font-weight:400}
.hero-title{position:absolute;left:162px;top:352px;font-family:"Oswald",sans-serif;font-size:40px;color:var(--blue);font-weight:500}
.hero-arrow{position:absolute;top:355px;width:32px;height:32px;border:2px solid rgba(255,255,255,.85);border-radius:50%}

/* steps */
.steps{position:absolute;left:0;top:627px;width:1200px;height:301px;background:var(--navy)}
.section-title{position:absolute;left:0;width:1200px;text-align:center;font-size:29px;color:var(--blue);font-family:"Oswald",sans-serif;font-weight:500}
.step{position:absolute;top:128px;display:flex;gap:18px}
.step h3{color:var(--blue);font-size:20px;margin-top:-4px;margin-bottom:8px}
.step p{color:#fff;font-size:11px;line-height:19px;width:200px}

/* flat fee */
.fee-frame{position:absolute;left:190px;top:1011px;width:345px;height:355px;border:12px solid var(--frame);border-left-color:var(--frame)}
.fee-photo{position:absolute;left:162px;top:981px;width:345px;height:355px;background:linear-gradient(135deg,#2a2f38 0%,#7d8795 45%,#e9edf2 70%,#bcc7d6 100%)}
.fee-text{position:absolute;left:564px;top:983px;width:472px}
.fee-text h2{font-size:29px;color:var(--blue);margin-bottom:10px}
.fee-lead{font-family:"Oswald",sans-serif;color:var(--blue);font-size:14.5px;line-height:21px;margin-bottom:12px}
.fee-body{font-size:10.6px;line-height:21px;color:var(--body)}
.btn-contact{position:absolute;left:564px;top:1306px;width:163px;height:44px;border-radius:22px;background:var(--navy);color:#fff;font-family:"Oswald",sans-serif;font-size:17px;display:flex;align-items:center;justify-content:center;gap:8px}

/* faq */
.faq{position:absolute;left:0;top:1407px;width:1200px;height:428px;background:linear-gradient(180deg,#1b2740 0%,#142038 60%,#1a2640 100%)}
.faq-list{position:absolute;left:162px;top:110px;width:431px}
.faq-item{height:42px;margin-bottom:8.5px;background:#fff;display:flex;align-items:center;font-size:14px;color:#333}
.faq-item .toggle{width:42px;height:42px;background:var(--blue);color:#fff;display:flex;align-items:center;justify-content:center;font-size:18px;margin-right:12px}
.faq-item.open{background:var(--blue);color:#fff;width:440px;clip-path:polygon(0 0,97% 0,100% 50%,97% 100%,0 100%)}
.faq-item.open .toggle{background:#1c84d6}
.faq-answer{position:absolute;left:608px;top:110px;width:433px;height:244px;background:var(--grey);padding:24px 16px;font-size:11px;line-height:19px;color:#333}
.faq-answer p+p{margin-top:16px}

/* know us */
.know-card{position:absolute;top:1931px;width:425px}
.know-photo{height:192px}
.know-card h3{font-size:23px;color:var(--blue);margin:20px 0 8px 4px}
.know-card p{font-size:11px;line-height:19px;color:#333}

/* footer */
.site-footer{position:absolute;left:0;top:2303px;width:1200px;height:225px;background:var(--navy);border-top:3px solid var(--blue)}
.news-title{position:absolute;left:162px;top:40px;font-family:"Oswald",sans-serif;font-size:26px;color:#fff;font-weight:400}
.field{position:absolute;top:41px;height:37px;background:var(--input);color:#fff;font-size:11px;padding:11px 12px}
.btn-signup{position:absolute;left:946px;top:41px;width:92px;height:37px;background:var(--blue);color:#fff;font-family:"Oswald",sans-serif;font-size:16px;display:flex;align-items:center;justify-content:center}
.foot-rule{position:absolute;left:162px;top:98px;width:876px;height:1px;background:#34415f}
.foot-div{position:absolute;top:125px;width:1px;height:70px;background:#34415f}
.foot-brand{position:absolute;left:162px;top:130px;width:142px;text-align:center;font-family:"Oswald",sans-serif;color:var(--blue);font-size:17px;line-height:20px}
.foot-brand i{display:block;width:22px;height:22px;background:var(--blue);margin:0 auto 8px}
.socials{position:absolute;left:415px;top:147px;display:flex;gap:5px}
.socials span{width:22px;height:22px;border:1.5px solid #fff;border-radius:50%}
.foot-nav{position:absolute;left:646px;top:139px;width:392px;display:flex;justify-content:space-between;color:#fff;font-family:"Montserrat",sans-serif;font-size:11px}
.copy{position:absolute;right:162px;top:164px;color:#fff;font-size:10.5px}
</style>
</head>
<body>

<header class="site-header">
  <div class="brand"><span class="brand-mark"></span>THE VELMAR HOLLOW GROUP</div>
  <div class="phone">
    <svg width="20" height="20" viewBox="0 0 24 24" fill="none" stroke="#2a9df4" stroke-width="1.8"><path d="M5 3h4l2 5-2.5 1.5a11 11 0 0 0 6 6L16 13l5 2v4a2 2 0 0 1-2 2A16 16 0 0 1 3 5a2 2 0 0 1 2-2z"/></svg>
    PHONE: 0800 555 0123
  </div>
  <nav class="main-nav">
    <span class="active">HOME</span><span>ABOUT</span><span>PROBATE</span><span>PROCESS</span><span>FAQ</span><span>CONTACT US</span><span>BLOG</span>
  </nav>
  <div class="nav-sep"></div>
  <svg class="search" width="14" height="14" viewBox="0 0 14 14" fill="none" stroke="#2a9df4" stroke-width="2"><circle cx="6" cy="6" r="4.5"/><path d="M9.5 9.5 13 13"/></svg>
</header>

<section class="hero" role="img" aria-label="Photo of a family with a child on his father's shoulders in a sunny green field">
</section>
<div class="hero-lead">Helping Californians deal with loss with</div>
<div class="hero-title">DIGNITY &amp; UNDERSTATING</div>
<div class="hero-arrow" style="left:38px"><svg width="28" height="28" viewBox="0 0 28 28"><path d="M16 9l-5 5 5 5" fill="none" stroke="#fff" stroke-width="2"/></svg></div>
<div class="hero-arrow" style="left:1129px"><svg width="28" height="28" viewBox="0 0 28 28"><path d="M12 9l5 5-5 5" fill="none" stroke="#fff" stroke-width="2"/></svg></div>

<section class="steps">
  <h2 class="section-title" style="top:38px">STEPS IN PROBATE</h2>
  <div class="step" style="left:162px">
    <svg width="62" height="82" viewBox="0 0 62 82"><circle cx="31" cy="20" r="17" fill="#fff"/><path d="M2 82V60a16 16 0 0 1 16-16h26a16 16 0 0 1 16 16v22z" fill="#fff"/></svg>
    <div><h3>1. GATHER</h3><p>Sed ut perspiciatis unde oloemn ns error sit voluptatem accusantulre mque laudantium, totam remis.</p></div>
  </div>
  <div class="step" style="left:470px">
    <svg width="78" height="78" viewBox="0 0 78 78"><g fill="#fff" transform="translate(39 39)"><rect x="-7" y="-39" width="14" height="78"/><rect x="-7" y="-39" width="14" height="78" transform="rotate(45)"/><rect x="-7" y="-39" width="14" height="78" transform="rotate(90)"/><rect x="-7" y="-39" width="14" height="78" transform="rotate(135)"/><circle r="29"/></g><circle cx="39" cy="39" r="11" fill="#1e2b4c"/></svg>
    <div><h3>2.IMPLEMENT</h3><p>Sed ut perspiciatis unde oloemn ns error sit voluptatem accusantulre mque laudantium, totam remis.</p></div>
  </div>
  <div class="step" style="left:780px">
    <svg width="76" height="76" viewBox="0 0 76 76"><circle cx="38" cy="38" r="37" fill="#fff"/><path d="M25 25l26 26M51 25 25 51" stroke="#1e2b4c" stroke-width="6"/></svg>
    <div><h3>3. CLOSE</h3><p>Sed ut perspiciatis unde oloemn ns error sit voluptatem accusantulre mque laudantium, totam remis.</p></div>
  </div>
</section>

<div class="fee-frame"></div>
<div class="fee-photo" role="img" aria-label="Photo of hands passing a document across a desk"></div>
<section class="fee-text">
  <h2>FLAT-FEE PRICE &amp; SAVINGS</h2>
  <p class="fee-lead">Lorem ipsum dolor sit amet, consectetur adipiscing elit, sed do eiusmod tempor inidiunt labore et dol ore magna aliqunim ad minim veniam, quis nostrud exercitatio</p>
  <p class="fee-body">Lorem ipsum dolor sit amet, consectetur adipiscing elit, sed do eiusmod tempor incididunt ut labore et dolore magna aliqua. Ut enim ad minim veniam, quis nostrud exercitation ullamco laboris nisi ut aliquip ex ea commodo consequat. Duis aute irure dolor in reprehenderit in voluptate velit esse cillum dolore eu fugiat nulla pariatur. Excepteur sint occaecat cupidatat non proident, sunt in culpa qui officia deserunt mollit anm id est labLorem ipsum dolor sit amet, consectetur adipiscing elit, sed do eiusmod tempor incididunt ut labore et dolore magna aliqua.nim ad minim veniam, quis nostrud exercitation ullamco laboris nisi ut aliquip ex ea commodo consequuis aute irure dolor in reprehen-derit in voluptate velit esse cillum dolore eu fugiat nulla pariatur. Excepteur sint occaecat cupidatat non proident, sunt in culpa qui officia deseruntm id est labore dolo.</p>
</section>
<div class="btn-contact">CONTACT US <svg width="16" height="16" viewBox="0 0 16 16"><circle cx="8" cy="8" r="6.5" fill="none" stroke="#fff" stroke-width="1.5"/><path d="M6.5 5v6l4-3z" fill="#fff"/></svg></div>

<section class="faq">
  <h2 class="section-title" style="top:38px">YOU HAVE QUESTIONS</h2>
  <div class="faq-list">
    <div class="faq-item open"><span class="toggle">&minus;</span>Lorem ipsum dolor sit um dolor sit amorpsum?</div>
    <div class="faq-item"><span class="toggle">+</span>Lorem ipsum dolor sit amet, consectetur adipiscing?</div>
    <div class="faq-item"><span class="toggle">+</span>Sed psum dolor sitorem ipsum dolor sit ametetur?</div>
    <div class="faq-item"><span class="toggle">+</span>Lorem ipsum dolor sit amet, consectetur adipiscing?</div>
    <div class="faq-item"><span class="toggle">+</span>Sed psum dolor sit aum dolor sit morpsum?</div>
  </div>
  <div class="faq-answer">
    <p>Sed ut perspiciatis unde omnis iste natus error sit voluptatemccusa lorntiumd oloremque laudantium, totam rem aperiam, eaque ipsa quae ab illo inventore veritatiasi archectoSed ut perspiciatis unde omnis iste natus error sit volupt atem cusantium doloremque laudantium, totam rem aperiam.</p>
    <p>Sed ut perspiciatis unde omnis iste natus error sit voluptatemccusa lorntium doloremque laudantium, totam rem aperiam, eaque ipsa quae ab illo inventore veritatiasi archectoSed ut perspiciatis unde omnis iste natus error sit volupt atem cusantium doloremque laudantium, totam rem aperiam.</p>
  </div>
</section>

<h2 class="section-title" style="top:1866px">GET TO KNOW US</h2>
<article class="know-card" style="left:162px">
  <div class="know-photo" role="img" aria-label="Photo of a hand stamping and signing papers on a desk" style="background:linear-gradient(160deg,#3a2a24 0%,#f1efec 45%,#d9d4cf 75%,#7a3322 100%)"></div>
  <h3>What We Do</h3>
  <p>Sed ut perspiciatis unde omnis iste natus error sit voluptatemccusalore lorntiumd olore mque laudantium, totam rem aperiam, eaque ipsa quae ab illo inventoreerit atiasi archectoSed ut perspiciatis unde omnis iste natus error sit voluptatem ccu santium doloremque laudantium, totam rem aperiaed ut perspiciatis unde omnis iste natus error sit voluptatemccusa lorntium</p>
</article>
<article class="know-card" style="left:613px">
  <div class="know-photo" role="img" aria-label="Photo of people reviewing and signing a contract at a table" style="background:linear-gradient(150deg,#8aa37a 0%,#d8dccf 35%,#f3f2ee 60%,#6b4a3a 100%)"></div>
  <h3>Who We Are</h3>
  <p>Sed ut perspiciatis unde omnis iste natus error sit voluptatemccusalore lorntiumd olore mque laudantium, totam rem aperiam, eaque ipsa quae ab illo inventoreerit atiasi archectoSed ut perspiciatis unde omnis iste natus error sit voluptatem ccu santium doloremque laudantium, totam rem aperiaed ut perspiciatis unde omnis iste natus error sit voluptatemccusa lorntium</p>
</article>

<footer class="site-footer">
  <div class="news-title">Newsletter Signup</div>
  <div class="field" style="left:369px;width:280px">Name:</div>
  <div class="field" style="left:657px;width:280px">Email:</div>
  <div class="btn-signup">SIGNUP</div>
  <div class="foot-rule"></div>
  <div class="foot-brand"><i></i>THE VELMAR<br>HOLLOW GROUP</div>
  <div class="foot-div" style="left:350px"></div>
  <div class="socials"><span></span><span></span><span></span><span></span></div>
  <div class="foot-div" style="left:590px"></div>
  <nav class="foot-nav"><span>HOME</span><span>ABOUT</span><span>PROBATE</span><span>PROCESS</span><span>FAQ</span><span>CONTACT US</span><span>BLOG</span></nav>
  <div class="copy">© 2017 All Copyrights are reserved. Privacy Policy</div>
</footer>

</body>
</html>
```